Powerpoint design template for LUMOTEX for new digital platform

We would like to use a PowerPoint template, we would like to create a new page, we would like to create a new digital platform LUMOTEX for schools and parents for the creation of playful communication and educational tools for children to enhance their positive development, amaze them learn in a playful way. This platform is going to be the most creative, stimulating and innovative classroom, easy to use and fast to implement. Scrapbooking, collages ... Magazine, newsletters Diplomla / awards Slideshows Facebook Calendars Organizers Greetings Games ... This powerpoint template will be used essential to We are looking for a professional design, positioning our brand in the children market with an adult hearing. so you will need to find a good deal. Primary target: nurseries & schools from 0 to 18 years old and universities (in 2nd phase) Secondary target: small & medium businesses Third target: general public, and TPE If it is a color scheme, then it is suggested that it be marketed in Europe (UK, Italy, Spain) and in a 2nd Stage USA and other countries. multiple options for front page, insidious pages (multiple styles with limited text and extended text) and final contact page We need something to read, we can not do it too much, but we can not do it. , and inside pages aligned to our logo

Target Market(s)

Target 1; Education with teacher Target 2; parents and grandparents

Industry/Entity Type

Education

Font styles to use
Other font styles liked:
• not decided. but not too fancy

Requirements
Must have
• Multi page options for front page, page insides (multiple styles with limited text and extended text) and final page contact
Nice to have
• do not have a lot of ideas. We need something to read, we can not get away from it
Should not have
• not too fancy and busy: keep clarity & simplicity while reassuring on quality

```html
<!DOCTYPE html>
<html lang="en">
<head>
<meta charset="UTF-8">
<title>LUMOTEX – Content Slide</title>
<link rel="stylesheet" href="https://fonts.googleapis.com/css2?family=Montserrat:wght@700;800&family=Nunito+Sans:wght@400;700&display=swap">
<style>
  :root {
    --pink: #e8287c;
    --blue: #0aaeef;
    --orange: #f47b20;
    --lime: #cfd92e;
    --white: #ffffff;
    --ink: #2b2b2b;
    --num-blue: #8fd8f7;
    --num-orange: #f9bd8f;
    --num-lime: #e6ec97;
  }
  * { margin: 0; padding: 0; box-sizing: border-box; }
  html, body { width: 1200px; height: 900px; overflow: hidden; background: var(--white); }
  .slide {
    position: relative;
    width: 1200px;
    height: 900px;
    background: var(--white);
    font-family: "Nunito Sans", Arial, sans-serif;
    overflow: hidden;
  }
  .slide-header { position: absolute; left: 0; top: 0; width: 1200px; height: 134px; }
  .slide-title {
    position: absolute;
    left: 37px;
    top: 38px;
    font-family: "Nunito Sans", Arial, sans-serif;
    font-weight: 700;
    font-size: 44px;
    letter-spacing: 0.5px;
    color: var(--pink);
  }
  .brand {
    position: absolute;
    right: 22px;
    top: 32px;
    display: flex;
    align-items: center;
    gap: 10px;
  }
  .brand-mark { width: 22px; height: 22px; background: var(--lime); }
  .brand-text { display: flex; flex-direction: column; }
  .brand-name {
    font-weight: 700;
    font-size: 30px;
    line-height: 1;
    color: var(--ink);
    letter-spacing: 1px;
  }
  .brand-tagline {
    margin-top: 5px;
    font-size: 9px;
    line-height: 1.2;
    letter-spacing: 1.5px;
    color: var(--ink);
  }
  .section {
    position: absolute;
    left: 0;
    width: 1200px;
    color: var(--white);
  }
  .section--one { top: 135px; height: 250px; background: var(--blue); }
  .section--two { top: 389px; height: 254px; background: var(--orange); }
  .section--three { top: 648px; height: 252px; background: var(--lime); }
  .section-number {
    position: absolute;
    left: 26px;
    top: 18px;
    font-family: "Montserrat", Arial, sans-serif;
    font-weight: 800;
    font-size: 112px;
    line-height: 1;
  }
  .section--one .section-number { color: var(--num-blue); left: 38px; }
  .section--two .section-number { color: var(--num-orange); }
  .section--three .section-number { color: var(--num-lime); }
  .section-title {
    position: absolute;
    left: 138px;
    top: 18px;
    font-weight: 700;
    font-size: 34px;
    line-height: 1.3;
  }
  .section-body {
    position: absolute;
    left: 138px;
    top: 72px;
    width: 1050px;
    font-size: 22.5px;
    line-height: 36px;
  }
</style>
</head>
<body>
  <main class="slide">
    <header class="slide-header">
      <h1 class="slide-title">CONTENT TITLE HERE</h1>
      <div class="brand">
        <span class="brand-mark"></span>
        <div class="brand-text">
          <span class="brand-name">LUMOTEX</span>
          <span class="brand-tagline">YOUR TAGLINE<br>GOES HERE</span>
        </div>
      </div>
    </header>

    <section class="section section--one">
      <span class="section-number">1</span>
      <h2 class="section-title">Section Title Here</h2>
      <p class="section-body">Lemon drops oat cake oat cake sugar plum sweet gingerbread chocolate cake<br>gingerbread. Lemon drops oat cake oat cake sugar plum sweet Lemon drops oat cake oat cake<br>sugar plum sweet gingerbread chocolate gingerbread. Lemon drops oat cake oat cake sugar<br>plum sweet</p>
    </section>

    <section class="section section--two">
      <span class="section-number">2</span>
      <h2 class="section-title">Section Title Here</h2>
      <p class="section-body">Lemon drops oat cake oat cake sugar plum sweet gingerbread chocolate cake<br>gingerbread. Lemon drops oat cake oat cake sugar plum sweet Lemon drops oat cake oat cake<br>sugar plum sweet gingerbread chocolate gingerbread. Lemon drops oat cake oat cake sugar<br>plum sweet</p>
    </section>

    <section class="section section--three">
      <span class="section-number">3</span>
      <h2 class="section-title">Section Title Here</h2>
      <p class="section-body">Lemon drops oat cake oat cake sugar plum sweet gingerbread chocolate cake<br>gingerbread. Lemon drops oat cake oat cake sugar plum sweet Lemon drops oat cake oat cake<br>sugar plum sweet gingerbread chocolate gingerbread. Lemon drops oat cake oat cake sugar<br>plum sweet</p>
    </section>
  </main>
</body>
</html>
```